Home Remodeler Needs a Website!

Single page (plus contact form) website for small home remodeling company. He's got a few pictures he'd like on the site and needs some basic text. He likes clean, simple designs and is "more traditional" in his stylistic preferences. Most of his business comes from word-of-mouth advertising and so the site is just something he needs for people to feel more comfortable with his business.

Target Market(s)

People who want to remodel their homes

Coding

Coded - Design and coding required

Number of Pages Required

2 page

Requirements
Must have
• Main page to include some or all of the attached images, contact page. Neutral colors. Old domain: lindcroftmeadowbuild.com New domain: qm-ventureworks.com You can pull text from the old site or update it.
Should not have
• No loud colors/loud visual elements

```html
<!DOCTYPE html>
<html lang="en">
<head>
<meta charset="utf-8">
<title>Lindcroft Meadow Homes</title>
<link href="https://fonts.googleapis.com/css2?family=Roboto:wght@400;500;700;900&display=swap" rel="stylesheet">
<style>
:root{
  --blue:#4d6a85;
  --blue-dark:#3c566f;
  --blue-deep:#34495c;
  --orange:#a9875f;
  --gold:#cdb27a;
  --ink:#262626;
  --grey:#777;
  --line:#a3a3a3;
  --black:#1c1c1c;
  --white:#fff;
}
*{box-sizing:border-box;margin:0;padding:0}
html,body{width:1200px;height:3800px;overflow:hidden}
body{position:relative;font-family:'Roboto',Arial,sans-serif;color:var(--ink);background:var(--white)}
.abs{position:absolute}
/* header */
.site-header{position:absolute;left:0;top:0;width:1200px;height:81px;background:var(--white)}
.brand{left:88px;top:24px;font-size:26px;font-weight:700;color:var(--blue);letter-spacing:.3px}
.main-nav{left:490px;top:30px;display:flex;gap:52px;font-size:15px;color:#333}
.main-nav .active{color:var(--blue);border-bottom:2px solid var(--blue);padding-bottom:6px}
.search-icon{left:1094px;top:32px}
/* hero */
.hero{left:0;top:81px;width:1200px;height:510px;overflow:hidden}
.hero-photo{position:absolute;inset:0;background:linear-gradient(110deg,#3a3228 0%,#6a5a45 35%,#8b8a86 55%,#4a5564 80%,#38434f 100%)}
.hero-shade{position:absolute;inset:0;background:linear-gradient(90deg,rgba(0,0,0,.45),rgba(0,0,0,.05))}
.hero h1{left:85px;top:120px;font-size:43px;line-height:43px;font-weight:700;color:var(--white);width:480px}
.hero p{left:85px;top:228px;font-size:15px;line-height:26px;color:var(--white);width:440px}
.btn-start{left:85px;top:315px;width:138px;height:37px;background:var(--blue);color:var(--white);font-size:15px;font-weight:700;display:flex;align-items:center;justify-content:center}
.hero-curve{position:absolute;left:0;bottom:0}
/* section titles */
.section-title{position:absolute;left:0;width:1200px;text-align:center;font-size:38px;font-weight:700;color:var(--ink)}
.title-rule{position:absolute;left:570px;width:60px;height:2px;background:var(--blue)}
/* service cards */
.svc{position:absolute;width:325px;height:144px;border-radius:72px;background:var(--white);box-shadow:0 3px 10px rgba(0,0,0,.16)}
.svc-icon{position:absolute;left:7px;top:10px;width:124px;height:124px;border-radius:50%}
.svc h3{position:absolute;left:148px;top:24px;font-size:15px;font-weight:700}
.svc p{position:absolute;left:148px;top:52px;font-size:14px;line-height:26px;color:var(--grey);width:170px}
.svc a{position:absolute;left:148px;top:109px;font-size:14px;color:var(--blue);text-decoration:none}
.is-blue{background:var(--blue)}
.is-orange{background:var(--orange)}
/* about band */
.about-band{left:0;top:1203px;width:1200px;height:546px;overflow:hidden;background:var(--blue)}
.about-photo{position:absolute;left:560px;top:0;width:640px;height:546px;background:linear-gradient(135deg,#8fa3b8 0%,#c7cfd6 40%,#a69a8a 70%,#5e5448 100%)}
.about-band h2{left:83px;top:118px;font-size:39px;font-weight:700;color:var(--white)}
.about-rule{left:85px;top:178px;width:60px;height:2px;background:var(--white)}
.about-band p{left:85px;top:205px;width:530px;font-size:15px;line-height:28.5px;color:var(--white)}
.btn-outline{left:85px;top:373px;width:133px;height:45px;border:1px solid var(--white);color:var(--white);font-size:15px;font-weight:700;display:flex;align-items:center;justify-content:center}
/* package */
.pkg{position:absolute;top:1960px;width:328px;height:354px;background:var(--white);box-shadow:0 2px 8px rgba(0,0,0,.18)}
.pkg-photo{position:absolute;left:11px;top:11px;width:306px;height:162px}
.pkg h3{position:absolute;left:11px;top:196px;font-size:15px;font-weight:700}
.pkg p{position:absolute;left:11px;top:224px;width:300px;font-size:14px;line-height:26px;color:var(--grey)}
.pkg a{position:absolute;left:11px;top:312px;font-size:15px;font-weight:700;color:var(--blue);text-decoration:none;display:flex;align-items:center;gap:12px}
/* testimonials */
.testimonials{left:0;top:2406px;width:1200px;height:472px;background:linear-gradient(180deg,var(--blue-dark),var(--blue))}
.testimonials h2{left:0;top:60px;width:1200px;text-align:center;font-size:38px;font-weight:700;color:var(--white)}
.testimonials .rule-w{left:570px;top:121px;width:60px;height:2px;background:var(--white)}
.quote-text{left:290px;top:177px;width:650px;text-align:center;font-size:15px;line-height:26px;color:var(--white)}
.stars{left:540px;top:300px;display:flex;gap:6px}
.author{left:0;top:350px;width:1200px;text-align:center;font-size:15px;font-weight:700;color:var(--white)}
/* contact */
.field{position:absolute;height:46px;border:1px solid var(--line);font-size:14px;color:#333;padding:15px 16px}
.field.message{height:106px}
.btn-submit{left:501px;top:3321px;width:200px;height:43px;background:var(--blue);color:var(--white);font-size:15px;font-weight:700;display:flex;align-items:center;justify-content:center;gap:14px}
/* footer */
.footer{left:0;top:3448px;width:1200px;height:352px}
.foot-nav{left:84px;top:95px;display:flex;gap:26px;font-size:13px;color:var(--white)}
.email-box{left:84px;top:133px;width:350px;height:33px;background:var(--white);font-size:14px;color:#888;padding:8px 12px}
.contact-head{left:580px;top:94px;font-size:16px;color:var(--white)}
.contact-line{left:580px;display:flex;gap:12px;font-size:15px;color:var(--white);line-height:24px}
.foot-brand{left:808px;top:90px;font-size:25px;font-weight:700;color:#8fa6bc}
.copyright{left:810px;top:140px;font-size:15px;color:var(--white)}
</style>
</head>
<body>

<header class="site-header">
  <div class="abs brand">LINDCROFT MEADOW HOMES</div>
  <nav class="abs main-nav">
    <span class="active">Home</span><span>About Us</span><span>Services</span><span>Testimonials</span><span>Contact Us</span>
  </nav>
  <svg class="abs search-icon" width="16" height="16" viewBox="0 0 16 16"><circle cx="6.5" cy="6.5" r="4.5" fill="none" stroke="#333" stroke-width="2"/><line x1="10" y1="10" x2="14" y2="14" stroke="#333" stroke-width="2"/></svg>
</header>

<section class="abs hero">
  <div class="hero-photo" role="img" aria-label="Photo of a remodeled kitchen with stainless appliances and a farmhouse sink"></div>
  <div class="hero-shade"></div>
  <h1 class="abs">Welcome to Lindcroft Meadow Homes.</h1>
  <p class="abs">When you want affordable, quality home construction services; think of us to do the job.</p>
  <div class="abs btn-start">GET STARTED</div>
  <svg class="abs" style="left:50px;top:228px" width="16" height="24" viewBox="0 0 16 24"><polyline points="12,3 4,12 12,21" fill="none" stroke="#fff" stroke-width="3"/></svg>
  <svg class="abs" style="left:1136px;top:228px" width="16" height="24" viewBox="0 0 16 24"><polyline points="4,3 12,12 4,21" fill="none" stroke="#fff" stroke-width="3"/></svg>
  <svg class="abs" style="left:557px;top:426px" width="90" height="32" viewBox="0 0 90 32">
    <rect x="1" y="1" width="33" height="29" style="fill:var(--blue-deep);stroke:var(--blue)"/>
    <polyline points="22,15 12,15 17,10 12,15 17,20" fill="none" stroke="#c8d3de" stroke-width="2.5"/>
    <rect x="53" y="1" width="34" height="29" fill="none" stroke="#fff"/>
    <polyline points="64,15 75,15 70,10 75,15 70,20" fill="none" stroke="#fff" stroke-width="2.5"/>
  </svg>
  <svg class="hero-curve" width="1200" height="110" viewBox="0 0 1200 110" preserveAspectRatio="none">
    <path d="M0 40 Q600 130 1200 40 L1200 110 L0 110 Z" fill="#fff"/>
    <path d="M0 40 Q600 130 1200 40 L1200 46 Q600 136 0 46 Z" style="fill:var(--blue-dark)"/>
  </svg>
</section>

<h2 class="section-title" style="top:655px">SERVICES PROVIDING</h2>
<div class="title-rule" style="top:720px"></div>

<div class="svc" style="left:85px;top:793px"><div class="svc-icon is-blue" role="img" aria-label="Replacement service icon"></div><h3>REPLACEMENT</h3><p>Lorem ipsum dolor sit consectetur adipiscing.</p><a>READ MORE</a></div>
<div class="svc" style="left:437px;top:793px"><div class="svc-icon is-orange" role="img" aria-label="Roofing service icon"></div><h3>ROOFING</h3><p>Lorem ipsum dolor sit consectetur adipiscing.</p><a>READ MORE</a></div>
<div class="svc" style="left:789px;top:793px"><div class="svc-icon is-blue" role="img" aria-label="Electrical service icon"></div><h3>ELECTRICAL</h3><p>Lorem ipsum dolor sit consectetur adipiscing.</p><a>READ MORE</a></div>
<div class="svc" style="left:85px;top:973px"><div class="svc-icon is-orange" role="img" aria-label="Air conditioning service icon"></div><h3>AIR CONDITIONING</h3><p>Lorem ipsum dolor sit consectetur adipiscing.</p><a>READ MORE</a></div>
<div class="svc" style="left:437px;top:973px"><div class="svc-icon is-blue" role="img" aria-label="Painting service icon"></div><h3>PAINTING</h3><p>Lorem ipsum dolor sit consectetur adipiscing.</p><a>READ MORE</a></div>
<div class="svc" style="left:789px;top:973px"><div class="svc-icon is-orange" role="img" aria-label="Concrete work service icon"></div><h3>CONCRETE WORK</h3><p>Lorem ipsum dolor sit consectetur adipiscing.</p><a>READ MORE</a></div>

<section class="abs about-band">
  <div class="about-photo" role="img" aria-label="Photo of a remodeled bathroom with soaking tub and tiled walls"></div>
  <svg class="abs" style="left:0;top:0" width="700" height="546" viewBox="0 0 700 546">
    <polygon points="0,0 575,0 660,273 560,546 0,546" style="fill:var(--blue)"/>
    <polygon points="615,150 687,273 610,420 648,273" style="fill:var(--orange)"/>
  </svg>
  <h2 class="abs">DON'T TINKER AROUND</h2>
  <div class="abs about-rule"></div>
  <p class="abs">I have built my business with a partnership of clients, employees, subcontractors, suppliers and inspectors. Since each project is unique, this partnership brings creative ideas to your home.I have deep "hands on" history in construction from foundations to final finishing touches.We cultivate suppliers who deliver quality materials on time and without damage.</p>
  <div class="abs btn-outline">LEARN MORE</div>
</section>

<h2 class="section-title" style="top:1825px">ALL IN ONE PACKAGE</h2>
<div class="title-rule" style="top:1900px"></div>

<svg class="abs" style="left:50px;top:2126px" width="14" height="22" viewBox="0 0 14 22"><polyline points="11,2 3,11 11,20" fill="none" stroke="#222" stroke-width="2.5"/></svg>
<svg class="abs" style="left:1136px;top:2126px" width="14" height="22" viewBox="0 0 14 22"><polyline points="3,2 11,11 3,20" fill="none" stroke="#222" stroke-width="2.5"/></svg>

<article class="pkg" style="left:85px"><div class="pkg-photo" role="img" aria-label="Photo of a bright interior under new construction" style="background:linear-gradient(90deg,#b89a72,#e7e3dc 60%,#c8b396)"></div><h3>NEW CONSTRUCTION</h3><p>Lorem ipsum dolor sit amet, consectetur adipiscing elit, sed do eiusmod tempor incididunt ut labore et dolore magna.</p><a>READ MORE <svg width="14" height="14" viewBox="0 0 14 14"><circle cx="7" cy="7" r="7" style="fill:var(--blue)"/><polyline points="4,7 10,7 7,4 10,7 7,10" fill="none" stroke="#fff" stroke-width="1.6"/></svg></a></article>
<article class="pkg" style="left:435px"><div class="pkg-photo" role="img" aria-label="Photo of a remodeled kitchen with island and bar stools" style="background:linear-gradient(90deg,#8a9aa6,#e5e4df 50%,#7b5a3e)"></div><h3>REMODELING</h3><p>Lorem ipsum dolor sit amet, consectetur adipiscing elit, sed do eiusmod tempor incididunt ut labore et dolore magna.</p><a>READ MORE <svg width="14" height="14" viewBox="0 0 14 14"><circle cx="7" cy="7" r="7" style="fill:var(--blue)"/><polyline points="4,7 10,7 7,4 10,7 7,10" fill="none" stroke="#fff" stroke-width="1.6"/></svg></a></article>
<article class="pkg" style="left:785px"><div class="pkg-photo" role="img" aria-label="Photo of an open living area with wood floors" style="background:linear-gradient(180deg,#a8a59c,#d9d4c8 50%,#4a3526)"></div><h3>PORCHES AND DECKS</h3><p>Lorem ipsum dolor sit amet, consectetur adipiscing elit, sed do eiusmod tempor incididunt ut labore et dolore magna.</p><a>READ MORE <svg width="14" height="14" viewBox="0 0 14 14"><circle cx="7" cy="7" r="7" style="fill:var(--blue)"/><polyline points="4,7 10,7 7,4 10,7 7,10" fill="none" stroke="#fff" stroke-width="1.6"/></svg></a></article>

<section class="abs testimonials">
  <h2 class="abs">OUR TESTIMONIALS</h2>
  <div class="abs rule-w"></div>
  <svg class="abs" style="left:266px;top:160px" width="26" height="20" viewBox="0 0 26 20"><g style="fill:var(--gold)"><rect x="0" y="0" width="11" height="11"/><rect x="14" y="0" width="11" height="11"/><rect x="0" y="8" width="5" height="12"/><rect x="14" y="8" width="5" height="12"/></g></svg>
  <p class="abs quote-text">Lorem ipsum dolor sit amet, consectetur adipiscing elit, sed do eiusmod tempor incididunt ut labore et dolore magna aliqua. Ut enim ad minim veniam, quis nostrud exercitation ullamco laboris nisi ut aliquip ex ea commodo consequat. Duis aute irure dolor in reprehenderit in voluptate velit esse cillum dolore eu fugiat nulla pariatur.</p>
  <svg class="abs" style="left:908px;top:266px" width="26" height="20" viewBox="0 0 26 20"><g style="fill:var(--gold)"><rect x="1" y="9" width="11" height="11"/><rect x="15" y="9" width="11" height="11"/><rect x="7" y="0" width="5" height="12"/><rect x="21" y="0" width="5" height="12"/></g></svg>
  <div class="abs stars">
    <svg width="120" height="20" viewBox="0 0 120 20"><g style="fill:var(--gold)"><polygon id="s" points="10,1 12.6,7 19,7.4 14,11.6 15.6,18 10,14.5 4.4,18 6,11.6 1,7.4 7.4,7"/><use href="#s" x="25"/><use href="#s" x="50"/><use href="#s" x="75"/><use href="#s" x="100"/></g></svg>
  </div>
  <div class="abs author">DANA WHITLOCK</div>
</section>

<h2 class="section-title" style="top:2952px">CONTACT FORM</h2>
<div class="title-rule" style="top:3016px"></div>

<div class="field" style="left:139px;top:3057px;width:452px">First Name:</div>
<div class="field" style="left:610px;top:3057px;width:452px">Last Name:</div>
<div class="field" style="left:139px;top:3126px;width:452px">Email:</div>
<div class="field" style="left:610px;top:3126px;width:452px">Address:</div>
<div class="field message" style="left:139px;top:3187px;width:923px">Address:</div>
<div class="abs btn-submit">SUBMIT MESSAGE <svg width="14" height="14" viewBox="0 0 14 14"><circle cx="7" cy="7" r="7" fill="#fff"/><polyline points="4,7 10,7 7,4 10,7 7,10" fill="none" style="stroke:var(--blue)" stroke-width="1.6"/></svg></div>

<footer class="abs footer">
  <svg class="abs" style="left:0;top:0" width="1200" height="352" viewBox="0 0 1200 352" preserveAspectRatio="none">
    <path d="M0 48 Q600 -30 1200 48 L1200 352 L0 352 Z" style="fill:var(--black)"/>
    <path d="M0 48 Q600 -30 1200 48 L1200 42 Q600 -36 0 42 Z" style="fill:var(--blue)"/>
  </svg>
  <nav class="abs foot-nav"><span>Home</span><span>About Us</span><span>Services</span><span>Testimonials</span><span>Contact Us</span></nav>
  <div class="abs email-box">Enter Email Id:</div>
  <svg class="abs" style="left:398px;top:143px" width="14" height="14" viewBox="0 0 14 14"><circle cx="7" cy="7" r="7" style="fill:var(--blue)"/><polygon points="3,7 11,4 9,11 7,8" fill="#fff"/></svg>
  <div class="abs contact-head">Contact Us</div>
  <div class="abs contact-line" style="top:148px"><svg width="14" height="24" viewBox="0 0 14 24"><path d="M3 6 L6 6 L7 10 L5 11 Q7 15 9 16 L10 14 L14 15 L14 18 Q8 19 3 9 Z" fill="#fff"/></svg>555-014-2290</div>
  <div class="abs contact-line" style="top:203px"><svg width="14" height="24" viewBox="0 0 14 24"><rect x="1" y="7" width="12" height="9" fill="none" stroke="#fff" stroke-width="1.4"/><polyline points="1,7 7,12 13,7" fill="none" stroke="#fff" stroke-width="1.4"/></svg>info@lmh-build.com</div>
  <div class="abs contact-line" style="top:247px"><svg width="14" height="24" viewBox="0 0 14 24"><path d="M7 2 Q12 2 12 7 Q12 10 7 16 Q2 10 2 7 Q2 2 7 2 Z" fill="#fff"/><circle cx="7" cy="7" r="2" style="fill:var(--black)"/></svg><span>61Lorem &nbsp;consectetur<br>adipiscing amet elit,</span></div>
  <div class="abs foot-brand">LINDCROFT MEADOW HOMES</div>
  <div class="abs copyright">©Copyright 2021 Lindcroft Meadow Homes.com</div>
</footer>

</body>
</html>
```